Create Premium Wine Label Design

We are premium wine exporters from Australia. We are looking to introduce new brand " The Velmora" - in red wine, White wine and Sparkling wine to international market.

The sample label design for red wine ( Shiraz) is attached.

This is our luxury brand. We need a stunning wine label designs for (front, back and neck) that should be mostly in GOLD colour and design should be really eye catching.

We have provided sample design for front, back and neck labels. However, we are looking forward to see a completely new improvised design.

LOGO attached.

Front Label Design Specification:

* We would like to see designs that are in Gold colour.
* Wine Bottle size is standard: 750ml; we assume the same design can be resizable to different bottle sizes.
* Our design should suit both black, white and sparkling wine bottles(sample attached)
* Use our logo in the design (see attached - label sample)
* Content for front label (see attached).
* Design should include all information specified in the sample

Back Label Design
* All contents in the sample should be used ( sample attached)
* LOGO attached.

Neck Label Design
* Sample of Neck label attached, please provide similar or your own design.
* LOGO attached.

Image Samples:
* Samples of label designs we like (see attached)
* Sample for gold color (see attached)
* For bottle shapes (see attached)
* Front, Back and Neck Label Samples (see attached)

Target Market(s)

International Wine Market

Font styles to use
Decorative
Script

Requirements
Must have
• Must have golden color on front and back label

```html
<!DOCTYPE html>
<html lang="en">
<head>
<meta charset="UTF-8">
<title>The Velmora Shiraz 2018 – Front Label</title>
<link rel="stylesheet" href="https://fonts.googleapis.com/css2?family=Abril+Fatface&family=Cinzel:wght@600;700&family=Cinzel+Decorative:wght@700&family=Pacifico&display=swap">
<style>
  :root {
    --page: #ffffff;
    --label-black: #000000;
    --gold-deep: #8a6a12;
    --gold-mid: #d4a626;
    --gold-light: #f6e27a;
    --gold-flat: #d9ad2c;
    --pattern-grey: #3a3a3a;
    --vintage-white: #ffffff;
    --band-ink: #0b0b0b;
    --foil: linear-gradient(100deg, var(--gold-deep) 0%, var(--gold-mid) 22%, var(--gold-light) 45%, var(--gold-mid) 62%, #b8860b 80%, var(--gold-light) 100%);
  }
  * { margin: 0; padding: 0; box-sizing: border-box; }
  html, body {
    width: 1200px; height: 1200px; overflow: hidden;
    background: var(--page);
  }
  .canvas { position: relative; width: 1200px; height: 1200px; }

  .label {
    position: absolute;
    left: 229px; top: 80px;
    width: 742px; height: 1051px;
    background: var(--label-black);
    overflow: hidden;
  }

  .brand {
    position: absolute;
    top: 232px; left: 0; width: 100%;
    text-align: center;
    font-family: "Cinzel", serif;
    font-weight: 700;
    font-size: 36px;
    letter-spacing: 2px;
    color: var(--gold-flat);
  }

  .floral-field {
    position: absolute;
    left: 36px; top: 268px;
    width: 668px; height: 668px;
    border-radius: 50%;
    background: radial-gradient(circle, #2e2e2e 0%, #262626 55%, #161616 85%, rgba(0,0,0,0) 100%);
  }

  .foil-text {
    background: var(--foil);
    -webkit-background-clip: text;
    background-clip: text;
    color: transparent;
  }

  .varietal {
    position: absolute;
    top: 452px; left: 0; width: 100%;
    text-align: center;
    font-family: "Pacifico", cursive;
    font-size: 92px;
    line-height: 1.2;
  }

  .wine-name {
    position: absolute;
    top: 640px; left: 0; width: 100%;
    display: flex; justify-content: center; align-items: center;
    gap: 4px;
  }
  .wine-name__article {
    font-family: "Abril Fatface", serif;
    font-size: 26px;
    letter-spacing: 1px;
    writing-mode: vertical-rl;
    transform: rotate(180deg);
    line-height: 1;
  }
  .wine-name__title {
    font-family: "Abril Fatface", serif;
    font-size: 104px;
    line-height: 1;
    letter-spacing: 1px;
  }

  .vintage {
    position: absolute;
    top: 806px; left: 0; width: 100%;
    text-align: center;
    font-family: "Abril Fatface", serif;
    font-size: 92px;
    line-height: 1;
    color: var(--vintage-white);
  }

  .origin-band {
    position: absolute;
    left: 0; top: 970px;
    width: 100%; height: 62px;
    background: linear-gradient(100deg, #c79a22 0%, #f1d777 25%, #d8b03a 50%, #f5e08c 72%, #c99c26 100%);
    display: flex; align-items: center; justify-content: center;
  }
  .origin-band__text {
    font-family: "Cinzel Decorative", serif;
    font-weight: 700;
    font-size: 31px;
    color: var(--band-ink);
    letter-spacing: 1px;
  }
</style>
</head>
<body>
<main class="canvas">
  <section class="label">
    <div class="floral-field" role="img" aria-label="Grey line-drawn floral mandala pattern behind the wine name"></div>

    <div class="brand">Aurelian Cellars</div>

    <h2 class="varietal foil-text">Shiraz</h2>

    <h1 class="wine-name">
      <span class="wine-name__article foil-text">THE</span>
      <span class="wine-name__title foil-text">VELMORA</span>
    </h1>

    <p class="vintage">2018</p>

    <div class="origin-band">
      <span class="origin-band__text">Wine of Australia</span>
    </div>
  </section>
</main>
</body>
</html>
```